Direct to Consumer extended service contract business with a new disruptive business model needs a

We need a customized wordpress design for a company called 'Bright Harbor Assurance'.
We provide an innovative and unique service contract protection program direct to consumers. This program provides monthly coverage for all electronics purchased in the last 4 years and all electronics the consumer purchases in the future for a low monthly fee. The overall design should communicate a sense of legitimacy, ethics, and superior customer service and support (in an industry that has a huge PR issue to overcome).
Electronics is the first product group, other product groups with different price points to launch in the future..

Target Market(s)

All purchasers of electronic goods...all demographics

Industry/Entity Type

Electronics

Font styles to use
Sans Serif

Requirements
Must have
• Customer Testimonials
Industry News
Customer ratings
Blog posts
Call to action messaging
Like the functional elements and design of quillmesa.example (need to be better)
Nice to have
• Like to see video testimonials
Social network "whats trending related to electronics or service contract industry"
Easy way to register products for warranty

```html
<!DOCTYPE html>
<html lang="en">
<head>
<meta charset="utf-8">
<title>Bright Harbor Assurance</title>
<link href="https://fonts.googleapis.com/css2?family=Open+Sans:wght@400;600;700&display=swap" rel="stylesheet">
<style>
:root{
  --green:#17904a;
  --green-light:#2fb463;
  --dark:#2a2624;
  --darker:#1d1b1a;
  --ink:#222;
  --muted:#555;
  --pale:#dfe9e3;
  --white:#fff;
  --line:#d6d6d6;
}
*{box-sizing:border-box;margin:0;padding:0}
html,body{width:1200px;height:3607px;overflow:hidden}
body{font-family:"Open Sans",Arial,sans-serif;color:var(--ink);background:#fff}
.wrap{width:840px;margin:0 auto;position:relative}
.btn{display:inline-block;background:var(--green);color:#fff;font-weight:700;font-size:14px;text-transform:uppercase;text-align:center;line-height:42px;height:42px;padding:0 26px}
.btn-outline{background:transparent;border:2px solid #fff;line-height:38px}
.section-title{text-align:center;font-weight:700;font-size:22px;text-transform:uppercase;letter-spacing:.5px}
.section-title em{font-style:normal;color:var(--green)}

/* header */
.site-header{height:89px;background:var(--darker);position:relative;overflow:hidden}
.site-header .nav-band{position:absolute;top:0;left:433px;right:0;height:89px;background:var(--green);clip-path:polygon(40px 0,100% 0,100% 100%,0 100%)}
.brand{position:absolute;left:190px;top:30px;display:flex;align-items:center;gap:10px;color:#fff;font-weight:700;font-size:16px}
.brand .mark{width:22px;height:22px;background:#fff}
.main-nav{position:absolute;left:488px;top:0;height:89px;display:flex;align-items:center;gap:38px}
.main-nav a{color:#fff;font-weight:600;font-size:14px;text-transform:uppercase;text-decoration:none}

/* hero */
.hero{height:493px;position:relative;background:linear-gradient(110deg,#d8b6a6 0%,#e9d6c6 25%,#f3efe7 45%,#c9d79a 75%,#8fae4e 100%)}
.hero-card{position:absolute;left:183px;top:195px;width:640px;height:137px;background:rgba(255,255,255,.82);padding:18px 30px}
.hero-card h1{font-size:21px;font-weight:400;color:#222}
.hero-card p{font-size:16px;margin:4px 0 14px}
.hero-card p strong{color:var(--green)}
.hero-card .btn{height:36px;line-height:36px;font-size:13px}
.dots{display:flex;gap:8px;justify-content:center}
.dots span{width:10px;height:10px;border-radius:50%;background:#222}
.dots span.on{background:var(--green)}
.hero .dots{position:absolute;left:0;right:0;top:470px}

/* cta */
.cta-bar{height:84px;background:var(--dark)}
.cta-bar .wrap{display:flex;justify-content:space-between;align-items:center;height:84px}
.cta-bar h2{color:#bdbdbd;font-size:27px;font-weight:700}
.cta-bar h2 em{font-style:normal;color:var(--green-light)}
.cta-bar .btn{width:208px}

/* welcome */
.welcome{height:183px;padding-top:34px;text-align:center}
.welcome p{font-size:11px;line-height:16px;color:var(--muted);margin-top:18px;padding:0 0}

/* services */
.services{height:353px;background:var(--pale);padding-top:34px}
.cards{display:flex;gap:20px;margin-top:24px}
.service{width:195px}
.service .photo{height:188px;position:relative}
.service .cap{font-size:12px;font-weight:600;text-align:center;line-height:34px;text-transform:uppercase}
.service.active .cap{background:var(--green);color:#fff}
.service .overlay{position:absolute;inset:0;background:rgba(20,20,20,.55);color:#fff;font-size:12px;font-weight:600;text-align:center;padding:50px 20px 0;text-transform:uppercase;line-height:18px}
.service .plus{width:34px;height:34px;border-radius:50%;background:var(--green);margin:0 auto 8px;position:relative}
.service .plus:before,.service .plus:after{content:"";position:absolute;background:#fff;left:50%;top:50%;transform:translate(-50%,-50%)}
.service .plus:before{width:16px;height:3px}.service .plus:after{width:3px;height:16px}

/* plans */
.plans-head{height:49px;background:var(--green);color:#fff;line-height:49px}
.plan{text-align:center;color:#fff;padding-top:58px}
.plan-electronics{height:332px;background:linear-gradient(180deg,#3b2a20,#2b1f19 60%,#3a2b22)}
.plan-vehicle{height:317px;background:linear-gradient(180deg,#23272d,#15181c)}
.plan h3{font-size:16px;font-weight:600;text-transform:uppercase}
.plan p{font-size:12px;line-height:26px;color:#ddd;margin-top:16px}
.plan h4{font-size:16px;font-weight:600;margin:18px 0 26px;text-transform:uppercase}
.plan .actions{display:flex;justify-content:center;gap:43px}
.plan .btn{width:166px;font-size:12px}

/* news */
.news{height:373px;padding-top:24px}
.news .cards{margin-top:26px}
.news-item{width:195px;position:relative;padding-top:20px}
.news-item .photo{height:185px}
.news-item .date{position:absolute;top:0;left:50%;transform:translateX(-50%);width:78px;height:60px;background:var(--green);color:#fff;text-align:center;border:3px solid #fff;line-height:1.1;padding-top:6px}
.news-item .date b{font-size:20px;display:block}.news-item .date span{font-size:14px}
.news-item h3{font-size:12.5px;font-weight:700;text-align:center;line-height:19px;margin-top:14px;text-transform:uppercase}

/* ratings */
.feedback{height:377px;background:var(--pale);padding-top:36px}
.feedback .wrap{display:flex;justify-content:space-between}
.col-title{font-size:17px;font-weight:700;text-transform:uppercase}
.col-title em{font-style:normal;color:var(--green)}
.ratings{width:380px}
.carousel{display:flex;align-items:center;justify-content:space-between;margin-top:20px;padding:0 10px}
.carousel svg{width:18px;height:40px}
.rating-photo{width:210px;height:118px}
.ratings .center{text-align:center}
.ratings h4{color:var(--green);font-size:16px;font-weight:700;margin-top:10px;text-transform:uppercase}
.stars{display:flex;justify-content:center;gap:2px;margin:4px 0}
.stars svg{width:26px;height:26px}
.ratings small{font-size:11px;color:var(--muted);display:block}
.ratings .btn{margin-top:12px;font-size:12px;height:40px;line-height:40px}
.testimonials{width:418px}
.quote{display:flex;gap:12px;padding:18px 0;border-bottom:1px solid var(--line)}
.quote .avatar{width:72px;height:72px;border-radius:50%;flex:none}
.quote p{font-size:11px;line-height:18px;color:var(--muted)}
.quote b{font-size:11px;font-weight:600;color:#222}
.testimonials .dots{justify-content:flex-end;margin-top:20px}

/* blog */
.blog{height:436px;background:linear-gradient(180deg,#262626,#121212);padding-top:36px;text-align:center}
.blog .section-title{display:inline-block;color:#fff;background:#111;padding:4px 26px;border-radius:20px}
.blog .cards{margin-top:20px}
.post{width:195px}
.post .photo{height:188px}
.post h3{color:#fff;font-size:12.5px;font-weight:700;margin-top:12px;text-transform:uppercase}
.post time{display:block;color:var(--green-light);font-size:16px;font-weight:700;margin-top:4px}
.blog .btn{margin-top:30px;font-size:12px;height:40px;line-height:40px}

/* contact */
.contact{height:449px;padding-top:26px}
.contact .cols{display:flex;justify-content:space-between;margin-top:22px}
.info{width:400px}
.contact h3{font-size:15px;font-weight:700;text-transform:uppercase}
.info ul{list-style:none;margin-top:18px}
.info li{display:flex;gap:14px;margin-bottom:14px;font-size:11px;line-height:17px;color:#444}
.info li svg{width:20px;height:20px;flex:none}
.info li b{display:block;font-weight:600;text-transform:uppercase}
.social{display:flex;gap:6px;margin-top:8px}
.social span{width:20px;height:20px;border-radius:50%;background:#3a7fc4}
.social span:nth-child(5){background:#d9582c}.social span:nth-child(6){background:#c43a2c}
.mail-form{width:410px}
.field{border:1px solid var(--line);height:46px;font-size:11px;color:#999;padding:15px 14px;margin-top:12px}
.row{display:flex;gap:12px}.row .field{flex:1}
.field.msg{height:132px}
.mail-form .btn{display:block;width:100%;margin-top:12px;height:48px;line-height:48px}

/* footer */
.site-footer{height:72px;background:var(--dark);color:#bbb;font-size:11px}
.site-footer .wrap{display:flex;justify-content:space-between;align-items:center;height:72px}
.site-footer nav{display:flex;gap:26px}
</style>
</head>
<body>

<header class="site-header">
  <div class="nav-band"></div>
  <div class="brand"><span class="mark"></span>Bright Harbor Assurance</div>
  <nav class="main-nav">
    <a>Home</a><a>About Us</a><a>Plans</a><a>News</a><a>Tesmonials</a><a>Contact Us</a>
  </nav>
</header>

<section class="hero" role="img" aria-label="Photo of hands typing on a white laptop in a bright room">
  <div class="hero-card">
    <h1>All your Products are protected for that Low Monthly Fee.</h1>
    <p>Dont' buy anymore <strong>In-Store</strong> service Plans</p>
    <span class="btn">Learn More</span>
  </div>
  <div class="dots"><span></span><span class="on"></span><span></span></div>
</section>

<section class="cta-bar">
  <div class="wrap">
    <h2>GET YOUR BRIGHT HARBOR <em>ASSURANCE</em> TODAY!</h2>
    <span class="btn">Signup Now!</span>
  </div>
</section>

<section class="welcome">
  <div class="wrap">
    <h2 class="section-title">Welcome to Bright Harbor <em>Assurance</em></h2>
    <p>Duis autem vel eum iriure dolor in hendrerit in vulputate velit esse molestie consequat, vel illum dolore eu feugiat nulla facilisis at vero eros et accumsan et iusto odio dignissim qui blandit praesent luptatum zzril delenit augue duis dolore te feugait nulla facilisi. Nam liber tempor cum soluta nobis eleifend option congue nihil imperdiet doming id quod mazim placerat facer possim assum.<br>Typi non habent claritatem insitam; est usus legentis in iis qui facit eorum claritatem. Investigationes demonstraverunt lectores legere me lius.</p>
  </div>
</section>

<section class="services">
  <div class="wrap">
    <h2 class="section-title">Our <em>Services</em></h2>
    <div class="cards">
      <div class="service"><div class="photo" role="img" aria-label="Photo of hands holding a tablet" style="background:linear-gradient(135deg,#5a4332,#2c2520)"></div><div class="cap">Lorem ipsum dolor sit</div></div>
      <div class="service active"><div class="photo" role="img" aria-label="Photo of a person using a smartphone" style="background:linear-gradient(135deg,#6b5a4d,#3a322c)"><div class="overlay"><div class="plus"></div>Lorem ipsum dolor sit amet, consectetuer adipiscing elit</div></div><div class="cap">Lorem ipsum dolor sit</div></div>
      <div class="service"><div class="photo" role="img" aria-label="Photo of a child using a laptop" style="background:linear-gradient(135deg,#c9c4bc,#8a7c6e)"></div><div class="cap">Lorem ipsum dolor sit</div></div>
      <div class="service"><div class="photo" role="img" aria-label="Photo of hands holding a smartphone" style="background:linear-gradient(135deg,#e3dcd6,#a8958a)"></div><div class="cap">Lorem ipsum dolor sit</div></div>
    </div>
  </div>
</section>

<section>
  <h2 class="section-title plans-head">Our Plans</h2>
  <div class="plan plan-electronics" role="img" aria-label="Background photo of tablets and a coffee cup on a wooden desk">
    <div class="wrap">
      <h3>Electronics Protection Plan</h3>
      <p>Ut wisi enim ad minim veniam, quis nostrud exerci tation ullamcorper suscipit lobortis nisl ut aliquip ex ea commodo consequat. Duis autem vel eum iriure dolor in hendrerit in vulputate velit esse molestie consequat, vel illum dolore eu feugiat nulla facilisis at vero eros et accumsan et iusto odio dignissim qui blandit praesent luptatum zzril delenit augue duis dolore te feugait nulla facilisi.</p>
      <h4>All for just $29.97 per month plus a one-time $30 membership fee</h4>
      <div class="actions"><span class="btn btn-outline">More Details</span><span class="btn">Sign Up Today!</span></div>
    </div>
  </div>
  <div class="plan plan-vehicle" role="img" aria-label="Background photo of a dark car front">
    <div class="wrap">
      <h3>Vehicle Protection Plan</h3>
      <p>Ut wisi enim ad minim veniam, quis nostrud exerci tation ullamcorper suscipit lobortis nisl ut aliquip ex ea commodo consequat. Duis autem vel eum iriure dolor in hendrerit in vulputate velit esse molestie consequat, vel illum dolore eu feugiat nulla facilisis at vero eros et accumsan et iusto odio dignissim qui blandit praesent luptatum zzril delenit augue duis dolore te feugait nulla facilisi.</p>
      <h4>All for just a low fixed monthly fee plus a one-time membership fee</h4>
      <div class="actions"><span class="btn btn-outline">More Details</span><span class="btn">Sign Up Today!</span></div>
    </div>
  </div>
</section>

<section class="news">
  <div class="wrap">
    <h2 class="section-title">Latest <em>News</em></h2>
    <div class="cards">
      <article class="news-item"><div class="photo" role="img" aria-label="Photo of hands on a keyboard and mouse" style="background:linear-gradient(135deg,#e7e2de,#9a8a80)"></div><div class="date"><b>10</b><span>OCT</span></div><h3>Ut wisi enim ad minim veniam, quis nostrud exerci tation ullamcorper</h3></article>
      <article class="news-item"><div class="photo" role="img" aria-label="Photo of a person writing beside a laptop" style="background:linear-gradient(135deg,#f1eeea,#b7aba0)"></div><div class="date"><b>10</b><span>OCT</span></div><h3>Eodem modo typi, qui nunc nobis videntur parum clari, fiant sollemnes in futurum</h3></article>
      <article class="news-item"><div class="photo" role="img" aria-label="Photo of a person typing on a laptop" style="background:linear-gradient(135deg,#8c8580,#3c3733)"></div><div class="date"><b>10</b><span>OCT</span></div><h3>Mirum est notare quam litt era gothica, quam nunc puta mus parum claram</h3></article>
      <article class="news-item"><div class="photo" role="img" aria-label="Photo of hands holding a smartphone over a laptop" style="background:linear-gradient(135deg,#6f7f96,#2f3644)"></div><div class="date"><b>10</b><span>OCT</span></div><h3>Typi non habent claritatem insitam est usus legentis in iis qui facit eorum</h3></article>
    </div>
  </div>
</section>

<section class="feedback">
  <div class="wrap">
    <div class="ratings">
      <h2 class="col-title">Customer <em>Ratings</em></h2>
      <div class="carousel">
        <svg viewBox="0 0 18 40"><path d="M15 2 3 20l12 18" fill="none" stroke="#666" stroke-width="2"/></svg>
        <div class="rating-photo" role="img" aria-label="Photo of an app store storefront sign" style="background:linear-gradient(135deg,#3a3a3a,#111)"></div>
        <svg viewBox="0 0 18 40"><path d="M3 2l12 18L3 38" fill="none" stroke="#666" stroke-width="2"/></svg>
      </div>
      <div class="center">
        <h4>Orchard App Shelf</h4>
        <div class="stars">
          <svg viewBox="0 0 24 24"><path d="M12 2l3 7 7 .6-5.4 4.7 1.7 7.2L12 17.8 5.7 21.5l1.7-7.2L2 9.6 9 9z" fill="#e9a41b"/></svg>
          <svg viewBox="0 0 24 24"><path d="M12 2l3 7 7 .6-5.4 4.7 1.7 7.2L12 17.8 5.7 21.5l1.7-7.2L2 9.6 9 9z" fill="#e9a41b"/></svg>
          <svg viewBox="0 0 24 24"><path d="M12 2l3 7 7 .6-5.4 4.7 1.7 7.2L12 17.8 5.7 21.5l1.7-7.2L2 9.6 9 9z" fill="#e9a41b"/></svg>
          <svg viewBox="0 0 24 24"><path d="M12 2l3 7 7 .6-5.4 4.7 1.7 7.2L12 17.8 5.7 21.5l1.7-7.2L2 9.6 9 9z" fill="#e9a41b"/></svg>
          <svg viewBox="0 0 24 24"><path d="M12 2l3 7 7 .6-5.4 4.7 1.7 7.2L12 17.8 5.7 21.5l1.7-7.2L2 9.6 9 9z" fill="#999"/></svg>
        </div>
        <small>4 AVERAGE ON 7000+ REVIEWS</small>
        <span class="btn">Read the Reviews</span>
      </div>
    </div>
    <div class="testimonials">
      <h2 class="col-title">Customer <em>Testimonials</em></h2>
      <div class="quote">
        <div class="avatar" role="img" aria-label="Video testimonial thumbnail" style="background:radial-gradient(circle,#3fae6a,#1e7a43)"></div>
        <div><p>"Quis aute iure reprehenderit in voluptate velit esse cillum dolore eu fugiat nulla pariatur. Stet clita kasd gubergren, no sea takimat, lorem ipsum sit."</p><b>Dana Whitfield, CEO</b></div>
      </div>
      <div class="quote">
        <div class="avatar" role="img" aria-label="Customer portrait" style="background:radial-gradient(circle,#9a9a9a,#4a4a4a)"></div>
        <div><p>"Quis aute iure reprehenderit in voluptate velit esse cillum dolore eu fugiat nulla pariatur. Stet clita kasd gubergren, no sea takimat, lorem ipsum sit."</p><b>Dana Whitfield, CEO</b></div>
      </div>
      <div class="dots"><span class="on"></span><span></span><span></span></div>
    </div>
  </div>
</section>

<section class="blog">
  <div class="wrap">
    <h2 class="section-title">Blog Posts</h2>
    <div class="cards">
      <article class="post"><div class="photo" role="img" aria-label="Photo of hands typing on a phone" style="background:linear-gradient(135deg,#eee,#9c8f86)"></div><h3>Ut wisi enim ad minim</h3><time>10 OCT 2014</time></article>
      <article class="post"><div class="photo" role="img" aria-label="Photo of a hand holding a smartphone against blue sky" style="background:linear-gradient(135deg,#3f86d6,#1b3f7a)"></div><h3>Claritas est etiam processus</h3><time>10 OCT 2014</time></article>
      <article class="post"><div class="photo" role="img" aria-label="Photo of a person driving a car" style="background:linear-gradient(135deg,#b7a48a,#5d4f40)"></div><h3>Mirum est notare quam</h3><time>10 OCT 2014</time></article>
      <article class="post"><div class="photo" role="img" aria-label="Photo of a tablet on an orange background" style="background:linear-gradient(135deg,#f08a2c,#c24f14)"></div><h3>Lorem ipsum dolor sit</h3><time>10 OCT 2014</time></article>
    </div>
    <span class="btn">View All</span>
  </div>
</section>

<section class="contact">
  <div class="wrap">
    <h2 class="section-title">Contact Us</h2>
    <div class="cols">
      <div class="info">
        <h3>Get in Touch</h3>
        <ul>
          <li><svg viewBox="0 0 20 20"><path d="M10 1a6 6 0 0 0-6 6c0 5 6 12 6 12s6-7 6-12a6 6 0 0 0-6-6zm0 8.5A2.5 2.5 0 1 1 10 4.5a2.5 2.5 0 0 1 0 5z" fill="#17904a"/></svg><div><b>Address :</b>4410 W. Seagrove Avenue Suite 212 Port Alder,<br>FL 33190, USA</div></li>
          <li><svg viewBox="0 0 20 20"><path d="M5 2l3 4-2 2a11 11 0 0 0 6 6l2-2 4 3-2 3C9 18 2 11 2 4z" fill="#17904a"/></svg><div><b>Phone :</b>(855) 555-0147</div></li>
          <li><svg viewBox="0 0 20 20"><rect x="5" y="2" width="10" height="5" fill="#17904a"/><rect x="2" y="7" width="16" height="8" rx="1" fill="#17904a"/><rect x="5" y="12" width="10" height="6" fill="#fff" stroke="#17904a" stroke-width="1.5"/></svg><div><b>Fax :</b>(855) 555-0183</div></li>
          <li><svg viewBox="0 0 20 20"><rect x="2" y="4" width="16" height="12" fill="#17904a"/><path d="M2 4l8 7 8-7" fill="none" stroke="#fff" stroke-width="1.5"/></svg><div><b>Email :</b>support@brightharbor.example</div></li>
        </ul>
        <h3>Stay Connected</h3>
        <div class="social"><span></span><span></span><span></span><span></span><span></span><span></span></div>
      </div>
      <form class="mail-form">
        <h3>Send Mail</h3>
        <div class="field">Name</div>
        <div class="row"><div class="field">Email Address</div><div class="field">Phone</div></div>
        <div class="field msg">Message</div>
        <span class="btn">Submit</span>
      </form>
    </div>
  </div>
</section>

<footer class="site-footer">
  <div class="wrap">
    <nav><span>Support</span><span>Privacy Policy</span><span>Terms &amp; Conditions</span><span>Contact Us</span></nav>
    <span>© 2014 Bright Harbor Assurance. All Rights Reserved.</span>
  </div>
</footer>

</body>
</html>
```